Modern Business Card

Modern professional business card with more than just logo and demographic info. Something memorable.

We are a trendy/modern chiropractic group with an emphasis on neurology, hence the minimalist-type brain logo. We want to convey that modern and technical aspect with professionalism and the elite nature of our practice environment.

```html
<!DOCTYPE html>
<html lang="en">
<head>
<meta charset="utf-8">
<title>Cortex Spine Studio – Business Card</title>
<link rel="stylesheet" href="https://fonts.googleapis.com/css2?family=Tinos:wght@400;700&display=swap">
<style>
  :root {
    --backdrop: #1d1d1f;
    --card: #ffffff;
    --ink: #111111;
    --muted: #6b6b6b;
    --brand-blue: #4a7fc1;
    --band: #0a0a0a;
  }
  * { box-sizing: border-box; margin: 0; padding: 0; }
  html, body {
    width: 1200px; height: 900px; overflow: hidden;
    background: var(--backdrop);
    font-family: "Tinos", "Times New Roman", serif;
    color: var(--ink);
  }
  .stage {
    position: relative; width: 1200px; height: 900px;
  }
  .card {
    position: absolute; left: 250px;
    width: 700px; height: 400px;
    background: var(--card);
    overflow: hidden;
    box-shadow: 0 12px 30px rgba(0,0,0,.55);
  }
  .card--front { top: 40px; }
  .card--back { top: 465px; }

  /* wordmark */
  .wordmark {
    position: absolute;
    display: flex; align-items: center; gap: 16px;
  }
  .wordmark__square {
    width: 34px; height: 34px; background: var(--brand-blue);
  }
  .wordmark__name {
    font-weight: 700; font-size: 40px; letter-spacing: 1px;
    text-transform: uppercase; color: var(--ink); line-height: 1;
  }
  .card--front .wordmark { left: 70px; top: 70px; }
  .card--back .wordmark { left: 50%; top: 150px; transform: translateX(-50%); }
  .card--back .wordmark__name { font-size: 46px; }
  .card--back .wordmark__square { width: 40px; height: 40px; }

  /* front details */
  .divider {
    position: absolute; left: 50px; top: 195px;
    width: 430px; height: 1px; background: var(--ink);
  }
  .accent-block {
    position: absolute; right: 0; top: 120px;
    width: 200px; height: 110px;
    background: var(--brand-blue);
    border-radius: 55px 0 0 55px;
  }
  .address {
    position: absolute; left: 50px; top: 215px;
    display: flex; gap: 10px; font-size: 17px; line-height: 1.35;
  }
  .address svg { flex: none; margin-top: 2px; }
  .person {
    position: absolute; right: 60px; top: 250px; text-align: right;
  }
  .person__name {
    font-weight: 700; font-size: 28px; letter-spacing: 1.5px; text-transform: uppercase;
  }
  .person__role {
    font-size: 16px; letter-spacing: 2px; color: var(--muted); text-transform: uppercase;
    margin-top: 2px;
  }
  .contact {
    position: absolute; right: 60px; top: 322px;
    list-style: none; text-align: right; font-size: 15px; line-height: 1.45;
  }
  .contact li { display: flex; justify-content: flex-end; align-items: center; gap: 10px; }
  .contact svg { flex: none; }

  /* back band */
  .web-band {
    position: absolute; left: 0; right: 0; top: 318px; height: 34px;
    background: var(--band); color: #ffffff;
    display: flex; align-items: center; justify-content: center;
    font-size: 15px; letter-spacing: 9px; text-transform: uppercase;
  }
</style>
</head>
<body>
<main class="stage">

  <section class="card card--front">
    <div class="wordmark">
      <span class="wordmark__square"></span>
      <span class="wordmark__name">Cortex Spine Studio</span>
    </div>

    <div class="accent-block"></div>
    <div class="divider"></div>

    <div class="address">
      <svg width="16" height="20" viewBox="0 0 16 20" aria-hidden="true">
        <path d="M8 0a7 7 0 0 0-7 7c0 5 7 13 7 13s7-8 7-13a7 7 0 0 0-7-7zm0 10a3 3 0 1 1 0-6 3 3 0 0 1 0 6z" fill="var(--brand-blue)"/>
      </svg>
      <p>PO Box 48 Hillcrest Vale<br>NSW 2790</p>
    </div>

    <div class="person">
      <p class="person__name">Daniel Hart</p>
      <p class="person__role">Chiropractor</p>
    </div>

    <ul class="contact">
      <li>02 5550 1847
        <svg width="16" height="16" viewBox="0 0 16 16" aria-hidden="true">
          <path d="M3.5 1l2.5 3-1.5 2c1 2 2.5 3.5 4.5 4.5l2-1.5 3 2.5-1.5 2.5C7 14 2 9 1 2.5z" fill="var(--brand-blue)"/>
        </svg>
      </li>
      <li>daniel@cortexspine.com
        <svg width="16" height="16" viewBox="0 0 16 16" aria-hidden="true">
          <rect x="1" y="3" width="14" height="10" fill="var(--brand-blue)"/>
          <path d="M1 3l7 6 7-6" fill="none" stroke="#fff" stroke-width="1.3"/>
        </svg>
      </li>
      <li>www.cortexspine.com
        <svg width="16" height="16" viewBox="0 0 16 16" aria-hidden="true">
          <g fill="none" stroke="var(--brand-blue)" stroke-width="1.3">
            <circle cx="8" cy="8" r="6.5"/>
            <ellipse cx="8" cy="8" rx="3" ry="6.5"/>
            <path d="M1.5 8h13M2.5 5h11M2.5 11h11"/>
          </g>
        </svg>
      </li>
    </ul>
  </section>

  <section class="card card--back">
    <div class="wordmark">
      <span class="wordmark__square"></span>
      <span class="wordmark__name">Cortex Spine Studio</span>
    </div>
    <div class="web-band">www.cortexspine.com</div>
  </section>

</main>
</body>
</html>
```